Commercial Rooftop Solar business needs a website

We need a website with fantastic appeal for a new company based in Melbourne called Tallow Ridge Energy. We design and install solar energy systems for commercial applications across Australia. Our market is to focus on small to medium businesses looking for solar solutions, but we will also provide our service for residential customers. We would like a beautiful 'front page' feel to our home page, using photographs of solar PV systems and/or natural imagery. Our logo uses the colours orange and black, which could easily be echoed in photographic imagery of sunset and sunrise, for example. The design should communicate quiet confidence and professionalism to a corporate marketplace.

NEW POINTS FOR BRIEF: This design also needs to be flexible to allow for additional future content, including a Support page with sub pages, FAQ's, and a Blog.

As part of this design project, we will require the coding for the website to be completed by the designer.

We have seen some websites, which we like the look and feel of: these are listed below.

brightvanepower.com.au:

• Beautiful images underlaying brief text selling points.
• Simple ‘front cover’ style home page with elegant drop-down menu, stylish simple font style.
• Home page invites exploration through the menu links, rather than trying to provide all the information up front.
• Company logo and name in the top left hand corner, contact details accessible at top right hand, seems consistent in most sites.

kelpworks.com.au

rumbofield.com:
• Same element as the others is the front-page style home page with beautiful images underlying text.

We have a webpage that we started uploading content to. You can use some of the content there in your designs: www.tallowridgeenergy.com.au

Technical Specifications:
PAGES:

Home

About Us

Solutions - Commercial
- Residential

Products - Solar Panels - Vorla Heron, Vorla TELD, Vorla QB
- Solar Inverters - Kestamo, BrilQuill
- Monitoring systems - Dunmere Metrics
- Batteries - RW

- Datasheets have been provided for reference but if it's too much work, you can use generic text and we will provide content later.

Contact Us

FUTURE PAGES (Please consider in structure, where links could be placed):

Support

FAQ's

Blog.

We could provide some content for the Support page soon, but the Blog and FAQ's are future pages which we don't want highlighted in the design as we don't yet have content.

Phone: 1800 7 BIRCH
Email: sales@tallowridgeenergy.com.au

Currently, I do not have images and text available. Please
use placeholders in the meantime. The final text and images will be uploaded for the winner once a winning design has been selected.

Target Market(s)

Primary focus is on small to medium sized business owners. Those owners will have a house which may be suitable for solar so we want to cater to residential deeper in the website.

Industry/Entity Type

Solar Energy

Coding

Coded - Design and coding required

Number of Pages Required

5+ page

Colors
f78f20
0255a3

Requirements
Must have
• Logo as per attachments.
Nice to have
• Logo can have alternate colours Eg. White on Orange or Black etc. provided colour correct logo is shown somewhere eg. footer or contact page.
• In the active site, I'd like to have:
• Very slowly zooming images - barely perceptible.
• Title text that rolls into place
• Subtle movements
• See https://plumtally.com.au/ for example

```html
<!DOCTYPE html>
<html lang="en">
<head>
<meta charset="utf-8">
<title>Tallow Ridge Energy</title>
<link href="https://fonts.googleapis.com/css2?family=Open+Sans:ital,wght@0,400;0,600;0,700;1,400&family=Raleway:wght@500;600;700&display=swap" rel="stylesheet">
<style>
:root{
  --orange:#ef6322;
  --orange-soft:#f28a4c;
  --ink:#1f1f1f;
  --text:#6f6f6f;
  --muted:#9a9a9a;
  --line:#d9d9d9;
  --panel:#f5f5f5;
  --white:#ffffff;
}
*{box-sizing:border-box;margin:0;padding:0}
html,body{width:1200px;height:3321px;overflow:hidden}
body{position:relative;background:var(--white);font-family:"Open Sans",sans-serif;color:var(--text)}
.section-title{position:absolute;left:0;width:1200px;text-align:center;font-family:"Raleway",sans-serif;font-weight:700;font-size:35px;color:var(--ink);letter-spacing:.5px}
.title-rule{position:absolute;left:560px;width:80px;height:3px;background:var(--orange)}

/* hero */
.hero{position:absolute;left:0;top:0;width:1200px;height:571px;overflow:hidden;
  background:
    radial-gradient(ellipse 260px 150px at 600px 440px,rgba(255,214,120,.95),rgba(255,170,60,.55) 45%,rgba(255,140,40,0) 100%),
    radial-gradient(ellipse 700px 120px at 600px 470px,rgba(240,150,50,.75),rgba(240,150,50,0) 100%),
    linear-gradient(90deg,rgba(20,20,30,.55) 0%,rgba(20,20,30,0) 25%,rgba(20,20,30,0) 75%,rgba(20,20,30,.55) 100%),
    linear-gradient(180deg,#3a3946 0%,#4d4650 22%,#6e5a54 42%,#a9743e 62%,#d08a34 74%,#8a5a30 84%,#4a3428 93%,#2a2325 100%)}
.hero-shade{position:absolute;inset:0;background:rgba(0,0,0,.12)}
.brand{position:absolute;left:77px;top:42px;display:flex;align-items:center;gap:12px;color:var(--white);font-family:"Raleway",sans-serif;font-weight:600;font-size:24px}
.brand-dot{width:34px;height:34px;border-radius:50%;background:var(--white)}
.nav{position:absolute;top:50px;left:447px;display:flex;gap:26px;font-family:"Raleway",sans-serif;font-weight:600;font-size:14px;color:var(--white)}
.nav .active{color:var(--orange)}
.nav-phone{position:absolute;left:947px;top:44px;display:flex;align-items:center;gap:12px;color:var(--white);font-size:15px}
.phone-badge{width:30px;height:30px;border-radius:50%;background:var(--orange);display:flex;align-items:center;justify-content:center}
.hero-title{position:absolute;top:172px;left:0;width:1200px;text-align:center;font-family:"Raleway",sans-serif;font-weight:700;font-size:60px;color:var(--white);letter-spacing:1px}
.hero-sub{position:absolute;top:256px;left:240px;width:720px;text-align:center;font-size:24px;line-height:40px;color:var(--white)}
.hero-btn{position:absolute;left:505px;top:365px;width:190px;height:47px;border:2px solid var(--white);border-radius:4px;color:var(--white);font-family:"Raleway",sans-serif;font-weight:700;font-size:14px;display:flex;align-items:center;justify-content:center;letter-spacing:.5px}
.hero-arrow{position:absolute;top:275px}
.scroll-cue{position:absolute;left:583px;top:486px}

/* welcome */
.intro{position:absolute;left:220px;top:750px;width:760px;text-align:center;font-size:12px;line-height:26px;color:var(--text)}
.feature{position:absolute;width:330px;height:90px}
.feature-icon{position:absolute;left:0;top:0;width:84px;height:84px;border-radius:50%;border:2px solid #e3e3e3;display:flex;align-items:center;justify-content:center}
.feature-name{position:absolute;left:100px;top:8px;font-family:"Raleway",sans-serif;font-weight:600;font-size:19px;color:var(--ink)}
.feature-text{position:absolute;left:100px;top:42px;width:210px;font-size:12px;line-height:22px;color:var(--muted)}

/* solutions */
.solutions{position:absolute;left:0;top:1160px;width:1200px;height:784px;background:var(--panel)}
.solution-photo{position:absolute;width:474px;height:260px;border:5px solid var(--white);box-shadow:0 0 0 1px #e4e4e4}
.photo-commercial{background:
    radial-gradient(ellipse 90px 60px at 310px 112px,rgba(255,246,200,1),rgba(255,210,110,.8) 40%,rgba(255,170,70,0) 100%),
    radial-gradient(ellipse 320px 70px at 300px 118px,rgba(255,190,80,.7),rgba(255,190,80,0) 100%),
    linear-gradient(180deg,#e98a3e 0%,#f3a650 28%,#f6b757 42%,#e4773a 50%,#b65a50 62%,#8c4a5c 78%,#62405a 100%)}
.photo-residential{background:
    radial-gradient(ellipse 260px 70px at 110px 30px,rgba(214,170,70,.8),rgba(214,170,70,0) 100%),
    radial-gradient(ellipse 300px 60px at 360px 20px,rgba(150,130,70,.6),rgba(150,130,70,0) 100%),
    linear-gradient(160deg,rgba(0,0,0,0) 0%,rgba(0,0,0,0) 55%,rgba(30,30,34,.55) 100%),
    linear-gradient(180deg,#b9a572 0%,#d8cfb5 20%,#b7c1cf 38%,#8e9bb2 55%,#6a7184 72%,#3d3d44 86%,#2b2b2f 100%)}
.solution-name{position:absolute;font-family:"Raleway",sans-serif;font-weight:700;font-size:25px;color:var(--ink)}
.solution-text{position:absolute;width:470px;font-size:12.5px;line-height:22px;color:var(--text)}
.more-btn{position:absolute;width:120px;height:40px;border:1px solid #bdbdbd;border-radius:4px;background:var(--white);color:var(--orange);font-family:"Raleway",sans-serif;font-weight:700;font-size:12px;display:flex;align-items:center;justify-content:center}

/* partners */
.partner{position:absolute;top:2119px;width:176px;height:86px;border:2px solid #dadada;background:var(--white);box-shadow:2px 2px 4px rgba(0,0,0,.15);display:flex;align-items:center;justify-content:center}
.partner-mark{width:132px;height:44px;border-radius:4px;background:linear-gradient(180deg,#b4b4b4,#9a9a9a)}

/* testimonials */
.testimonials{position:absolute;left:0;top:2298px;width:1200px;height:412px;
  background:
    radial-gradient(ellipse 260px 160px at 160px 80px,rgba(255,200,130,.55),rgba(255,200,130,0) 100%),
    radial-gradient(ellipse 300px 220px at 1000px 60px,rgba(190,70,20,.35),rgba(190,70,20,0) 100%),
    linear-gradient(180deg,#ed7031 0%,#ee6a2a 40%,#e2612a 70%,#d2572a 100%)}
.testimonials .section-title{color:var(--white);top:79px}
.testimonials .title-rule{background:var(--white);top:128px}
.quote{position:absolute;top:177px;width:330px}
.avatar{position:absolute;left:0;top:0;width:78px;height:78px;border-radius:50%;border:3px solid var(--white);background:linear-gradient(160deg,#e2d2c4,#a8968a)}
.quote-body{position:absolute;left:96px;top:0;width:226px;font-style:italic;font-size:11px;line-height:20px;color:var(--white)}
.quote-name{position:absolute;left:96px;top:110px;font-size:10px;font-weight:600;color:var(--white);text-transform:uppercase}
.quote-role{position:absolute;left:96px;top:126px;font-size:9px;font-style:italic;color:#ffe2d0}
.slide-btn{position:absolute;top:2533px;width:34px;height:34px;border-radius:50%;border:1.5px solid rgba(255,255,255,.8);display:flex;align-items:center;justify-content:center}

/* contact */
.sub-head{position:absolute;font-family:"Raleway",sans-serif;font-weight:600;font-size:19px;color:#333}
.field{position:absolute;border:1px solid #cfcfcf;background:var(--white);font-size:11px;color:#888;padding:8px 12px}
.submit{position:absolute;left:622px;top:3153px;width:104px;height:37px;border:1px solid #bdbdbd;border-radius:4px;color:var(--orange);font-family:"Raleway",sans-serif;font-weight:700;font-size:13px;display:flex;align-items:center;justify-content:center}
.info-row{position:absolute;left:797px;display:flex;align-items:flex-start;gap:20px;font-size:12px;line-height:20px;color:#555}
.info-icon{width:36px;height:36px;border-radius:50%;border:1.5px solid #e0e0e0;display:flex;align-items:center;justify-content:center;flex:none}
.socials{position:absolute;left:797px;top:3158px;display:flex;gap:9px}
.social{width:30px;height:30px;border-radius:50%}
.footer-rule{position:absolute;left:97px;top:3224px;width:1006px;height:1px;background:var(--line)}
.copyright{position:absolute;top:3260px;left:0;width:1200px;text-align:center;font-size:12px;color:#777}
.to-top{position:absolute;left:1070px;top:3256px}
</style>
</head>
<body>

<header class="hero" role="img" aria-label="City skyline and harbour at sunset">
  <div class="hero-shade"></div>
  <div class="brand"><span class="brand-dot"></span>Tallow Ridge Energy</div>
  <nav class="nav">
    <span class="active">HOME</span><span>ABOUT US</span><span>SOLUTIONS ▾</span><span>CONTACT US</span>
    <svg width="16" height="16" viewBox="0 0 16 16" style="margin-top:1px"><circle cx="6.5" cy="6.5" r="4.5" fill="none" stroke="#fff" stroke-width="2"/><line x1="10" y1="10" x2="14" y2="14" stroke="#fff" stroke-width="2"/></svg>
  </nav>
  <div class="nav-phone">
    <span class="phone-badge"><svg width="14" height="14" viewBox="0 0 24 24"><path d="M6.6 10.8a15 15 0 006.6 6.6l2.2-2.2c.3-.3.7-.4 1-.2 1.1.4 2.3.6 3.6.6.6 0 1 .4 1 1V20c0 .6-.4 1-1 1A17 17 0 013 4c0-.6.4-1 1-1h3.5c.6 0 1 .4 1 1 0 1.3.2 2.5.6 3.6.1.3 0 .7-.2 1z" fill="#fff"/></svg></span>
    <span>1 800 555 0142</span>
  </div>
  <svg class="hero-arrow" style="left:14px" width="14" height="24" viewBox="0 0 14 24"><path d="M12 2L2 12l10 10" fill="none" stroke="#fff" stroke-width="2"/></svg>
  <svg class="hero-arrow" style="left:1172px" width="14" height="24" viewBox="0 0 14 24"><path d="M2 2l10 10L2 22" fill="none" stroke="#fff" stroke-width="2"/></svg>
  <h1 class="hero-title">TALLOW RIDGE ENERGY</h1>
  <p class="hero-sub">We design and install solar energy systems for commercial applications across Australia</p>
  <div class="hero-btn">GET MORE INFO</div>
  <svg class="scroll-cue" width="34" height="50" viewBox="0 0 34 50"><rect x="2" y="2" width="30" height="46" rx="15" fill="none" stroke="#fff" stroke-width="2"/><path d="M11 16l6 6 6-6M11 25l6 6 6-6" fill="none" stroke="#fff" stroke-width="2"/></svg>
</header>

<section class="welcome">
  <h2 class="section-title" style="top:650px">WELCOME TO TALLOW RIDGE ENERGY</h2>
  <div class="title-rule" style="top:709px"></div>
  <p class="intro">Nemo enim ipsam voluptatem quia voluptas sit aspernatur aut odit aut fugit, sed quia consequuntur magni dolores eos qui ratione voluptatem sequi nesciunt neque dolorem ipsum quia dolor sit amet, consectetur, adipisci velit, sed quiauam</p>

  <div class="feature" style="left:97px;top:852px">
    <div class="feature-icon"><svg width="34" height="34" viewBox="0 0 34 34"><rect x="4" y="8" width="20" height="20" rx="2" fill="none" stroke="var(--orange)" stroke-width="2.5"/><path d="M14 20l2-6 12-12 4 4-12 12z" fill="var(--orange)"/></svg></div>
    <div class="feature-name">System Design</div>
    <p class="feature-text">At vero eos et accusamus et iusto odio dignissimos ducim</p>
  </div>
  <div class="feature" style="left:454px;top:852px">
    <div class="feature-icon"><svg width="36" height="36" viewBox="0 0 36 36"><circle cx="14" cy="20" r="8" fill="none" stroke="var(--orange)" stroke-width="5" stroke-dasharray="3 3"/><circle cx="14" cy="20" r="3" fill="var(--orange)"/><circle cx="27" cy="9" r="5" fill="none" stroke="var(--orange)" stroke-width="4" stroke-dasharray="2.5 2"/></svg></div>
    <div class="feature-name">Operational Management</div>
    <p class="feature-text">At vero eos et accusamus et iusto odio dignissimos ducim</p>
  </div>
  <div class="feature" style="left:815px;top:852px">
    <div class="feature-icon"><svg width="34" height="34" viewBox="0 0 34 34"><path d="M6 28l13-13" stroke="var(--orange)" stroke-width="5" stroke-linecap="round"/><circle cx="23" cy="11" r="7" fill="var(--orange)"/><circle cx="26" cy="8" r="3" fill="#fff"/></svg></div>
    <div class="feature-name">Installation</div>
    <p class="feature-text">At vero eos et accusamus et iusto odio dignissimos ducim</p>
  </div>
  <div class="feature" style="left:97px;top:989px">
    <div class="feature-icon"><svg width="36" height="36" viewBox="0 0 36 36"><circle cx="18" cy="18" r="8" fill="var(--orange)"/><g stroke="var(--orange)" stroke-width="2.5"><line x1="18" y1="2" x2="18" y2="7"/><line x1="18" y1="29" x2="18" y2="34"/><line x1="2" y1="18" x2="7" y2="18"/><line x1="29" y1="18" x2="34" y2="18"/><line x1="6" y1="6" x2="10" y2="10"/><line x1="26" y1="26" x2="30" y2="30"/><line x1="30" y1="6" x2="26" y2="10"/><line x1="6" y1="30" x2="10" y2="26"/></g></svg></div>
    <div class="feature-name">Solar Irrigation</div>
    <p class="feature-text">At vero eos et accusamus et iusto odio dignissimos ducim</p>
  </div>
  <div class="feature" style="left:454px;top:989px">
    <div class="feature-icon"><svg width="40" height="26" viewBox="0 0 40 26"><rect x="2" y="3" width="32" height="20" rx="2" fill="none" stroke="var(--orange)" stroke-width="2.5"/><rect x="34" y="9" width="4" height="8" fill="var(--orange)"/><rect x="6" y="7" width="24" height="12" fill="var(--orange)"/></svg></div>
    <div class="feature-name">Energy Storage</div>
    <p class="feature-text">At vero eos et accusamus et iusto odio dignissimos ducim</p>
  </div>
  <div class="feature" style="left:815px;top:989px">
    <div class="feature-icon"><svg width="30" height="38" viewBox="0 0 30 38"><path d="M15 3a11 11 0 00-7 19.5c1.5 1.3 2 2.5 2 4.5h10c0-2 .5-3.2 2-4.5A11 11 0 0015 3z" fill="none" stroke="var(--orange)" stroke-width="2.5"/><rect x="10" y="29" width="10" height="3" fill="var(--orange)"/><rect x="11" y="33" width="8" height="3" fill="var(--orange)"/></svg></div>
    <div class="feature-name">Feasibility Study</div>
    <p class="feature-text">At vero eos et accusamus et iusto odio dignissimos ducim</p>
  </div>
</section>

<section class="solutions">
  <h2 class="section-title" style="top:57px">OUR SOLUTIONS</h2>
  <div class="title-rule" style="top:113px"></div>
  <div class="solution-photo photo-commercial" style="left:100px;top:175px" role="img" aria-label="Solar panel field under a setting sun"></div>
  <div class="solution-photo photo-residential" style="left:629px;top:175px" role="img" aria-label="Solar panels mounted on a house roof with trees behind"></div>
  <h3 class="solution-name" style="left:100px;top:471px">COMMERCIAL</h3>
  <h3 class="solution-name" style="left:629px;top:471px">RESIDENTIAL</h3>
  <p class="solution-text" style="left:100px;top:540px">Nam libero tempore, cum soluta nobis est eligendi optio cumque nihil impedit quo minus id quod maxime placeat facere possimus, omnis voluptas amenda est, omnis dolor repellendus et voluptates repudi earum rerum hic tenetur sa piente delectus, ut aut rei voluptatib.</p>
  <p class="solution-text" style="left:629px;top:540px">Nam libero tempore, cum soluta nobis est eligendi optio cumque nihil impedit quo minus id quod maxime placeat facere possimus, omnis voluptas amenda est, omnis dolor repellendus et voluptates repudi earum rerum hic tenetur sa piente delectus, ut aut rei voluptatib.</p>
  <div class="more-btn" style="left:100px;top:664px">READ MORE &gt;&gt;</div>
  <div class="more-btn" style="left:629px;top:664px">READ MORE &gt;&gt;</div>
</section>

<section class="partners">
  <h2 class="section-title" style="top:2007px">OUR PARTNERS</h2>
  <div class="title-rule" style="top:2063px"></div>
  <div class="partner" style="left:98px"><span class="partner-mark"></span></div>
  <div class="partner" style="left:305px"><span class="partner-mark"></span></div>
  <div class="partner" style="left:512px"><span class="partner-mark"></span></div>
  <div class="partner" style="left:719px"><span class="partner-mark"></span></div>
  <div class="partner" style="left:925px"><span class="partner-mark"></span></div>
</section>

<section class="testimonials" role="img" aria-label="Orange-tinted city freeway at sunset behind client testimonials">
  <h2 class="section-title">TESTIMONIALS</h2>
  <div class="title-rule"></div>
  <div class="quote" style="left:97px">
    <div class="avatar" role="img" aria-label="Client portrait"></div>
    <p class="quote-body">“ At vero eos et accusamus et iustodio dignissimos ducimus qui blanditiispraesent ium voluptatum deleniti atque corrupti dolores et quas molestias.</p>
    <div class="quote-name">Marlo Penhaligon</div>
    <div class="quote-role">Finance Services Lead</div>
  </div>
  <div class="quote" style="left:441px">
    <div class="avatar" role="img" aria-label="Client portrait"></div>
    <p class="quote-body">“ At vero eos et accusamus et iustodio dignissimos ducimus qui blanditiispraesent ium voluptatum deleniti atque corrupti dolores et quas molestias.</p>
    <div class="quote-name">Teodor Vancliffe</div>
    <div class="quote-role">Regional Urban Fellow at the Institute</div>
  </div>
  <div class="quote" style="left:790px">
    <div class="avatar" role="img" aria-label="Client portrait"></div>
    <p class="quote-body">“ At vero eos et accusamus et iustodio dignissimos ducimus qui blanditiispraesent ium voluptatum deleniti atque corrupti dolores et quas molestias.</p>
    <div class="quote-name">Isla Brekkerton</div>
    <div class="quote-role">Creative Strategist | Business Owner</div>
  </div>
</section>
<div class="slide-btn" style="left:30px"><svg width="10" height="14" viewBox="0 0 10 14"><path d="M8 1L2 7l6 6" fill="none" stroke="#fff" stroke-width="2"/></svg></div>
<div class="slide-btn" style="left:1136px"><svg width="10" height="14" viewBox="0 0 10 14"><path d="M2 1l6 6-6 6" fill="none" stroke="#fff" stroke-width="2"/></svg></div>

<section class="contact">
  <h2 class="section-title" style="top:2809px">CONTACT US</h2>
  <div class="title-rule" style="top:2865px"></div>
  <h3 class="sub-head" style="left:97px;top:2899px">Contact form</h3>
  <h3 class="sub-head" style="left:797px;top:2899px">Contact Information</h3>
  <div class="field" style="left:97px;top:2965px;width:313px;height:33px">Name :</div>
  <div class="field" style="left:418px;top:2965px;width:310px;height:33px">Phone no :</div>
  <div class="field" style="left:97px;top:3011px;width:631px;height:33px">Email :</div>
  <div class="field" style="left:97px;top:3057px;width:631px;height:81px">Message :</div>
  <div class="submit">SUBMIT</div>

  <div class="info-row" style="top:2950px">
    <span class="info-icon"><svg width="14" height="18" viewBox="0 0 14 18"><path d="M7 1a6 6 0 00-6 6c0 4.5 6 10 6 10s6-5.5 6-10a6 6 0 00-6-6z" fill="none" stroke="var(--orange)" stroke-width="1.8"/><circle cx="7" cy="7" r="2" fill="var(--orange)"/></svg></span>
    <span>Tallow Ridge Energy<br>Flinders Lane, Melbourne, Australia</span>
  </div>
  <div class="info-row" style="top:3007px">
    <span class="info-icon"><svg width="14" height="14" viewBox="0 0 24 24"><path d="M6.6 10.8a15 15 0 006.6 6.6l2.2-2.2c.3-.3.7-.4 1-.2 1.1.4 2.3.6 3.6.6.6 0 1 .4 1 1V20c0 .6-.4 1-1 1A17 17 0 013 4c0-.6.4-1 1-1h3.5c.6 0 1 .4 1 1 0 1.3.2 2.5.6 3.6.1.3 0 .7-.2 1z" fill="var(--orange)"/></svg></span>
    <span style="line-height:36px">1 800 555 0142</span>
  </div>
  <div class="info-row" style="top:3054px">
    <span class="info-icon"><svg width="16" height="16" viewBox="0 0 16 16"><rect x="2" y="5" width="12" height="8" rx="1" fill="var(--orange)"/><rect x="4" y="1" width="8" height="4" fill="none" stroke="var(--orange)" stroke-width="1.5"/><rect x="5" y="9" width="6" height="2" fill="#fff"/></svg></span>
    <span style="line-height:36px">1 800 555 0199</span>
  </div>
  <div class="info-row" style="top:3101px">
    <span class="info-icon"><svg width="16" height="12" viewBox="0 0 16 12"><rect x="1" y="1" width="14" height="10" rx="1" fill="var(--orange)"/><path d="M1 2l7 5 7-5" fill="none" stroke="#fff" stroke-width="1.3"/></svg></span>
    <span style="line-height:36px">info@tallowridgeenergy.com.au</span>
  </div>
  <div class="socials">
    <span class="social" style="background:#3b5998"></span>
    <span class="social" style="background:#33a9e0"></span>
    <span class="social" style="background:#1f7bb6"></span>
    <span class="social" style="background:#cb2027"></span>
  </div>
</section>

<footer>
  <div class="footer-rule"></div>
  <p class="copyright">Copyright © 2017, Tallow Ridge Energy. All rights reserved.</p>
  <svg class="to-top" width="30" height="18" viewBox="0 0 30 18"><path d="M3 15L15 4l12 11" fill="none" stroke="#9a9a9a" stroke-width="2.5"/></svg>
</footer>

</body>
</html>
```